Under Morning Lantern website

I need a website to sell my t-shirt designs. I have around 5 designs I plan to sell on my initial launch, but only 3 photos at the moment. I would love a main page with the product images below maybe a large nicely designed header image, showing products with their sizes, item name/description, a way to add to cart and a review system like stars below each product image. Maybe a share option to Picturely, Facelog, Chirper, Pinterest, etc. would be cool too. Also on the main page under the product images a section showcasing my Picturely photos for the company. Then a section where I will include an About Me video from like Tuber. Lastly, on the main page an option to join my Mailing List at the footer with links to my Facelog and Picturely social accounts, links to pages (About Me, Shop, Picturely page, & Contact Us) as well as Track Order.

The other 4 pages will be for an About Me, which is the video I will make later that will be from Tuber. Then the Shop page. Then the Picturely page showcasing all the photos I plan to use to market the products, and a Contact Us Page.

I plan to possibly connect this to Shopify, so showcasing payment options (Palo, Birch Pay, Wayfarer, etc.) would be nice.

Lastly, I don't plan on doing returns/exchanges so maybe an area showing that would be nice too. ALL SALES FINAL

Mobile Friendly!

1st image is logo and other 4 images are t-shirt designs

Coded - Design and coding required

5+ page

• Separate pages, No Refunds (All Sales Final), Add to Cart, Way to Purchase

```html
<!DOCTYPE html>
<html lang="en">
<head>
<meta charset="utf-8">
<title>Under Morning Lantern – About Me</title>
<link rel="stylesheet" href="https://fonts.googleapis.com/css2?family=Poppins:wght@300;400;500;600&family=Roboto:wght@400;500&family=Oswald:wght@700&display=swap">
<style>
:root{
  --brand-blue:#00adee;
  --ink:#1b1b1b;
  --ink-soft:#333;
  --plum:#4a3a6d;
  --panel-grey:#f1f1f1;
  --footer-bg:#2b2b2b;
  --footer-text:#b9b9b9;
  --footer-head:#e6e6e6;
  --white:#fff;
}
*{margin:0;padding:0;box-sizing:border-box}
html,body{width:774px;height:1200px;overflow:hidden;background:var(--white)}
body{position:relative;font-family:'Roboto',sans-serif;color:var(--ink)}
.abs{position:absolute}

/* header */
.site-header{left:0;top:0;width:774px;height:202px;background:var(--brand-blue)}
.brand{left:77px;top:26px;width:116px;text-align:center;color:var(--ink)}
.brand-name{font-family:'Poppins',sans-serif;font-weight:600;font-size:27px;line-height:28px;letter-spacing:1px}
.brand-tag{font-family:'Poppins',sans-serif;font-weight:600;font-size:5.5px;letter-spacing:2px;color:var(--white);margin-top:2px}
.main-nav{left:277px;top:31px;width:221px;height:26px;background:var(--white);border-radius:13px;display:flex;align-items:center;padding-left:19px;gap:20px;font-size:8.5px;color:#666}
.main-nav .active{color:var(--ink);position:relative}
.main-nav .active::after{content:"";position:absolute;left:50%;bottom:-5px;width:2px;height:2px;margin-left:-1px;border-radius:50%;background:var(--ink)}
.track-link{left:615px;top:38px;font-size:9px;color:var(--white)}
.cart{left:677px;top:36px}
.cart-count{left:689px;top:31px;width:10px;height:10px;border-radius:50%;background:#143447;color:var(--white);font-size:6px;line-height:10px;text-align:center}
.page-title{left:0;width:774px;top:127px;text-align:center;font-family:'Roboto',sans-serif;font-weight:500;font-size:23px;color:var(--white)}
.crumbs{left:0;width:774px;top:159px;text-align:center;font-size:10px;color:var(--white);word-spacing:2px}
.crumbs span{margin:0 9px}

/* about */
.section-title{left:0;width:774px;top:246px;text-align:center;font-family:'Roboto',sans-serif;font-weight:500;font-size:23px;color:var(--plum)}
.section-title em{font-style:normal;color:var(--brand-blue)}
.title-rule{left:372px;top:276px;width:30px;height:1.5px;background:var(--brand-blue)}
.side-panel{top:389px;height:106px;background:var(--panel-grey)}
.video{left:124px;top:292px;width:526px;height:297px;background:#000;overflow:hidden}
.video-frame{position:absolute;inset:0 0 27px 0;background:linear-gradient(100deg,#b9aaa0 0%,#8a7c78 28%,#3e2f5a 45%,#3a2b55 58%,#1f5350 72%,#235a55 85%,#8c8a56 100%)}
.video-title{position:absolute;left:131px;top:27px;font-family:'Poppins',sans-serif;font-size:16px;color:rgba(255,255,255,.85)}
.play-btn{position:absolute;left:243px;top:108px}
.video-bar{position:absolute;left:0;bottom:0;width:526px;height:27px;background:#111;display:flex;align-items:center;font-family:'Poppins',sans-serif;font-size:7px;color:#ddd}
.progress{position:absolute;left:27px;top:12px;width:393px;height:2px;background:#333}
.progress i{display:block;width:85px;height:2px;background:#999}
.time{position:absolute;left:428px;top:9px}
.hd{position:absolute;left:501px;top:9px;color:var(--brand-blue);font-weight:600}

/* gallery */
.gallery-head{left:176px;top:626px;font-family:'Poppins',sans-serif;font-weight:600;font-size:18px;color:var(--ink-soft)}
.gallery-copy{left:176px;top:655px;width:430px;font-family:'Poppins',sans-serif;font-size:10.4px;line-height:13px;color:var(--ink-soft)}
.tile{display:block}

/* newsletter */
.news-title{left:0;width:774px;top:924px;text-align:center;font-family:'Poppins',sans-serif;font-size:20px;color:var(--ink)}
.news-sub{left:0;width:774px;top:955px;text-align:center;font-family:'Poppins',sans-serif;font-weight:300;font-size:7.5px;color:#555}
.news-field{left:169px;top:986px;width:436px;height:18px;border-bottom:1px solid #ccc;font-family:'Poppins',sans-serif;font-weight:300;font-size:6.5px;color:#aaa;display:flex;justify-content:space-between;padding-top:2px}

/* footer */
.site-footer{left:0;top:1039px;width:774px;height:161px;background:var(--footer-bg)}
.foot-head{font-size:10px;color:var(--footer-head)}
.foot-text{font-size:8.8px;color:var(--footer-text);line-height:14.5px}
.foot-links{list-style:none;font-size:8.8px;color:var(--footer-text);line-height:16px}
.foot-rule{top:1070px;width:1px;height:92px;background:#3a3a3a}
.foot-brand{left:555px;top:1084px;width:100px;text-align:center;color:var(--brand-blue)}
.foot-brand .brand-name{font-size:21px;line-height:22px}
.foot-brand .brand-tag{font-size:4.5px;margin-top:1px;color:var(--white)}
.socials{left:548px;top:1131px;width:114px;display:flex;justify-content:space-between;font-size:6px;color:#aaa}
</style>
</head>
<body>

<header class="abs site-header"></header>
<div class="abs brand"><div class="brand-name">U.M.L.</div><div class="brand-tag">UNDER MORNING LANTERN</div></div>
<nav class="abs main-nav"><span class="active">About</span><span>Shop</span><span>Picturely</span><span>Contact</span></nav>
<div class="abs track-link">Track Order</div>
<svg class="abs cart" width="16" height="16" viewBox="0 0 16 16" fill="none" stroke="#fff" stroke-width="1.1"><path d="M1 2h2.5l2 8h8l1.5-6H4.5"/><circle cx="6.5" cy="13" r="1.1"/><circle cx="12.5" cy="13" r="1.1"/></svg>
<div class="abs cart-count">0</div>
<h1 class="abs page-title">ABOUT ME</h1>
<div class="abs crumbs">Home<span>|</span>About Me</div>

<h2 class="abs section-title">ABOUT <em>ME</em></h2>
<div class="abs title-rule"></div>
<div class="abs side-panel" style="left:0;width:108px"></div>
<div class="abs side-panel" style="left:665px;width:109px"></div>

<div class="abs video">
  <div class="video-frame" role="img" aria-label="Video still: two printed t-shirts laid among flowers"></div>
  <div class="video-title">About UML Check out the video</div>
  <svg class="play-btn" width="42" height="42" viewBox="0 0 42 42"><circle cx="21" cy="21" r="21" fill="rgba(110,100,120,.75)"/><path d="M15 11v20l16-10z" fill="#fff"/></svg>
  <div class="video-bar">
    <svg style="position:absolute;left:10px;top:9px" width="8" height="9" viewBox="0 0 8 9"><path d="M0 0v9l7-4.5z" fill="#fff"/></svg>
    <div class="progress"><i></i></div>
    <span class="time">03:47 / 10:00</span>
    <svg style="position:absolute;left:484px;top:9px" width="10" height="9" viewBox="0 0 10 9" fill="#ddd"><path d="M0 3h2l3-3v9L2 6H0z"/><path d="M6.5 2.5q1.5 2 0 4M8 1q3 3.5 0 7" stroke="#ddd" fill="none"/></svg>
    <span class="hd">HD</span>
  </div>
</div>

<h2 class="abs gallery-head">Picturely</h2>
<p class="abs gallery-copy">Meet your fellow Humans! Show us your UML style on Chirper, Picturely or Facelog and tag @UML for a chance to win free tees and be featured on our site!</p>

<div class="abs tile" style="left:164px;top:701px;width:205px;height:190px;background:linear-gradient(#3a3d47,#3a3d47)" role="img" aria-label="Purple t-shirt on a dark background"></div>
<div class="abs tile" style="left:377px;top:701px;width:115px;height:92px;background:linear-gradient(135deg,#6f8da6,#59585a 60%,#3e3d3f)" role="img" aria-label="Woman wearing a graphic tank top against a rock wall"></div>
<div class="abs tile" style="left:500px;top:701px;width:110px;height:92px;background:linear-gradient(180deg,#e8e8e6,#b0a890 55%,#6e6650)" role="img" aria-label="Person in a black hoodie standing in a field"></div>
<div class="abs tile" style="left:377px;top:801px;width:115px;height:90px;background:linear-gradient(135deg,#5e6164,#8a8c8f 50%,#4a4c4f)" role="img" aria-label="Man in a white tee leaning on a stone wall"></div>
<div class="abs tile" style="left:500px;top:801px;width:110px;height:90px;background:linear-gradient(180deg,#b7c2c9,#8c9196 55%,#6d6a67)" role="img" aria-label="Woman in a dark hoodie sitting on a boardwalk"></div>

<h2 class="abs news-title">Join Our Newsletter</h2>
<p class="abs news-sub">Sale up to 20% off for your next purchase in this month!</p>
<div class="abs news-field"><span>Your email address</span><span>Subscribe</span></div>

<footer class="abs site-footer"></footer>
<div class="abs foot-head" style="left:99px;top:1067px">Contact Us</div>
<p class="abs foot-text" style="left:99px;top:1091px">Lorem Ipsum, is simply<br>dummy text of the</p>
<p class="abs foot-text" style="left:99px;top:1133px">+xxx xxxx xxxxx</p>
<p class="abs foot-text" style="left:99px;top:1155px">xxxxxxx@lanternmail.com</p>
<div class="abs foot-rule" style="left:260px"></div>
<div class="abs foot-head" style="left:342px;top:1068px">Contact Us</div>
<ul class="abs foot-links" style="left:342px;top:1091px"><li>Home</li><li>About</li><li>Services</li><li>Contact</li><li>Track Order</li></ul>
<div class="abs foot-rule" style="left:473px"></div>
<div class="abs foot-brand"><div class="brand-name">U.M.L.</div><div class="brand-tag">UNDER MORNING LANTERN</div></div>
<div class="abs socials"><span>Chirper</span><span>Plusly</span><span>Facelog</span><span>Tuber</span><span>Picturely</span></div>

</body>
</html>
```